Construction material supplies company business card ****

1. Full company name “K T Masonry Works Ltd”
I am after a Business card design for the company as a whole. We are better known in Solomon Islands as “K T Masonry” for short.

We are a building materials supplier of
Ready Mixed Concrete, Bricks and Blocks,
Quarry products- gravel, aggregates, sand etc.
Cement distributor/retailer of reputable brands.
Other prefab concrete products. Culverts, wave breakers, concrete retaining blocks etc.

2. Competitive Advantage over Competition: Quality, efficient, professional, dependable, reliable

3. We want people to feel trust worthy, high quality, strong when they see our brand

5. No preference to color. Maybe more sturdy and corporate. Not fancy.

Industry/Entity Type

CONSTRUCTION SUPPLY

Contact Information for Business Card

Name, Position, office phone mob phone, email

Requirements
Must have
• the company logo
Nice to have
• would like to see a mixture of designs, of with logo only and also with simple graphic designs to bring out the company whilst still have the strong sturdy professional feeling

```html
<!DOCTYPE html>
<html lang="en">
<head>
<meta charset="utf-8">
<title>K T Masonry – Business Card</title>
<link href="https://fonts.googleapis.com/css2?family=Michroma&family=Montserrat:wght@400;700&family=Arimo:wght@400&display=swap" rel="stylesheet">
<style>
  :root {
    --navy: #173f6b;
    --paper: #ffffff;
    --backdrop: #e6eaeb;
    --ink: #222222;
    --muted: #6b6b6b;
  }
  * { box-sizing: border-box; margin: 0; padding: 0; }
  html, body { width: 1200px; height: 900px; overflow: hidden; }
  body {
    background: var(--backdrop);
    display: flex;
    flex-direction: column;
    align-items: center;
    justify-content: center;
    gap: 56px;
  }
  .card {
    position: relative;
    width: 600px;
    height: 343px;
    background: var(--paper);
    border-bottom: 8px solid var(--navy);
    box-shadow: 0 6px 18px rgba(0,0,0,0.12);
    overflow: hidden;
  }
  .brand {
    display: flex;
    align-items: center;
    gap: 16px;
    color: var(--navy);
    font-family: "Michroma", sans-serif;
    white-space: nowrap;
  }
  .brand-mark {
    background: var(--navy);
    flex: none;
  }

  /* front: logo only */
  .card-front .brand {
    position: absolute;
    inset: 0;
    justify-content: center;
    font-size: 44px;
  }
  .card-front .brand-mark { width: 34px; height: 34px; }

  /* back: contact details */
  .card-back .brand {
    position: absolute;
    left: 40px;
    top: 44px;
    font-size: 30px;
  }
  .card-back .brand-mark { width: 24px; height: 24px; }
  .person {
    position: absolute;
    right: 44px;
    top: 132px;
    text-align: right;
  }
  .person-name {
    font-family: "Montserrat", sans-serif;
    font-weight: 700;
    font-size: 22px;
    color: var(--navy);
  }
  .person-role {
    font-family: "Arimo", sans-serif;
    font-size: 13px;
    color: var(--muted);
    margin-top: 2px;
  }
  .name-tab {
    position: absolute;
    right: 0;
    top: 128px;
    width: 9px;
    height: 48px;
    background: var(--navy);
    border-radius: 6px 0 0 6px;
  }
  .contact-list {
    position: absolute;
    right: 20px;
    top: 196px;
    list-style: none;
    font-family: "Arimo", sans-serif;
    font-size: 17px;
    color: var(--ink);
  }
  .contact-list li {
    display: flex;
    justify-content: flex-end;
    align-items: center;
    gap: 14px;
    height: 26px;
  }
  .contact-icon { width: 16px; height: 16px; flex: none; }
</style>
</head>
<body>

  <section class="card card-front" aria-label="Business card front">
    <div class="brand"><span class="brand-mark"></span>K T MASONRY</div>
  </section>

  <section class="card card-back" aria-label="Business card back">
    <div class="brand"><span class="brand-mark"></span>K T MASONRY</div>
    <span class="name-tab"></span>
    <div class="person">
      <p class="person-name">Peter Lamani</p>
      <p class="person-role">Director</p>
    </div>
    <ul class="contact-list">
      <li>555 204 1180
        <svg class="contact-icon" viewBox="0 0 16 16" fill="var(--navy)"><path d="M3 1.5l2.5 0 1 3.2-1.6 1.2c.8 1.8 2.2 3.2 4 4l1.2-1.6 3.2 1v2.5c0 .8-.7 1.5-1.5 1.5C6.5 13.3 2.7 9.5 1.5 3 1.5 2.2 2.2 1.5 3 1.5z"/></svg>
      </li>
      <li>555 204 1180
        <svg class="contact-icon" viewBox="0 0 16 16" fill="none" stroke="var(--navy)" stroke-width="1.6"><rect x="4" y="1" width="8" height="14" rx="1.5"/><line x1="7" y1="12.5" x2="9" y2="12.5"/></svg>
      </li>
      <li>info@ktmasonry.com
        <svg class="contact-icon" viewBox="0 0 16 16" fill="var(--navy)"><path d="M1 3h14v10H1z"/><path d="M1.5 3.5L8 9l6.5-5.5" stroke="#fff" stroke-width="1.2" fill="none"/></svg>
      </li>
      <li>www.ktmasonry.com
        <svg class="contact-icon" viewBox="0 0 16 16"><circle cx="8" cy="8" r="7" fill="var(--navy)"/><path d="M1.5 8h13M8 1.2c-2.5 2.8-2.5 10.8 0 13.6M8 1.2c2.5 2.8 2.5 10.8 0 13.6" stroke="#fff" stroke-width="1" fill="none"/></svg>
      </li>
    </ul>
  </section>

</body>
</html>
```